FinTech company looking to revamp and expand client-facing interface for our financial models

Pellworth Engines currently has a very simple website that allows clients to interact with our financial models. We are looking to completely redesign the current site and add several extra pages to provide extra functionality. We want the design to have a modern, slick feel, that will work on both a desktop or a tablet. It should be straightforward for clients to move between different pages at any time, and clear from the layout how to interact with the more advanced features. We have included screenshots of existing pages in the attached design brief, as well as sketches of the functionality required by the new pages, but can't provide a direct link to the current site.
Target Market(s)
Professional investors that will be paying to access the interface
Industry/Entity Type
Finance
Number of Pages Required
4 page
Colors
Designer to choose colors to be used in the design.
Look and feel
Each slider illustrates characteristics of the customer's brand and the style your logo design should communicate.

```html
<!DOCTYPE html>
<html lang="en">
<head>
<meta charset="utf-8">
<title>Korva – Models</title>
<link href="https://fonts.googleapis.com/css2?family=Open+Sans:wght@400;600;700&display=swap" rel="stylesheet">
<style>
:root{
  --navy:#04305e;
  --teal:#006b66;
  --teal-row:#e3f2ef;
  --black:#1c1c1c;
  --white:#ffffff;
  --band:#efefef;
  --tab-active:#cbcbcb;
  --text:#111111;
  --rule:#dcdcdc;
}
*{box-sizing:border-box;margin:0;padding:0}
html,body{width:1200px;height:678px;overflow:hidden}
body{font-family:"Open Sans",sans-serif;color:var(--text);
  background:linear-gradient(#f2f2f2 0,#f2f2f2 143px,#e9e9e9 150px,#f6f6f6 400px,#f8f8f8 678px);position:relative}
.topbar{position:absolute;left:0;top:0;width:1200px;height:55px;background:var(--white);box-shadow:0 2px 6px rgba(0,0,0,.08)}
.brand{position:absolute;left:67px;top:0;line-height:55px;font-weight:700;font-size:18px;letter-spacing:.3px}
.range,.nav{position:absolute;top:0;height:55px;display:flex;align-items:center;justify-content:center;font-weight:700;font-size:13px;border-right:1px solid #ececec}
.range.active,.nav.active{background:var(--navy);color:var(--white)}
.nav svg{margin-right:7px}
.subtab{position:absolute;background:var(--white);font-weight:600;font-size:12.5px;display:flex;align-items:center;justify-content:center;border-radius:4px 4px 0 0;box-shadow:0 -1px 3px rgba(0,0,0,.05)}
.subtab.active{background:var(--tab-active)}
.tab-more{position:absolute;left:1098px;top:111px;width:37px;height:32px;background:var(--white);display:flex;align-items:center;justify-content:center;border-radius:4px 4px 0 0}
.tab-add{position:absolute;left:1140px;top:111px;width:37px;height:32px;background:var(--navy);display:flex;align-items:center;justify-content:center;border-radius:4px 4px 0 0}
.export{position:absolute;left:1085px;top:184px;display:flex;align-items:center;font-weight:700;font-size:16px;color:var(--navy)}
.export svg{margin-right:6px}
.filters{position:absolute;left:0;top:235px;width:46px;height:176px;background:#dedede;border-radius:0 5px 5px 0}
.filters span{position:absolute;left:5px;top:88px;transform:rotate(-90deg) translate(-50%,0);transform-origin:0 0;font-weight:600;font-size:14px;letter-spacing:.5px}
.filters svg{position:absolute;left:34px;top:78px}
.models{position:absolute;left:97px;top:217px;width:1071px;border-collapse:collapse;table-layout:fixed;background:var(--white);border-radius:6px;overflow:hidden;box-shadow:0 2px 8px rgba(0,0,0,.12)}
.models th{height:65px;color:var(--white);font-weight:600;font-size:15.5px;background:var(--teal);border-right:1px solid rgba(255,255,255,.18)}
.models th.key{background:var(--black);border-right:1px solid #3a3a3a}
.models td{height:64.5px;font-size:15px;padding-left:4px;border-right:1px solid #eeeeee;line-height:1.45}
.models td.id{padding-left:16px}
.models td.sector{padding-left:17px}
.models tbody tr:nth-child(even) td{background:var(--teal-row)}
</style>
</head>
<body>
<header class="topbar">
  <div class="brand">KORVA</div>
  <div class="range active" style="left:180px;width:83px">250D</div>
  <div class="range" style="left:263px;width:83px">83D</div>
  <div class="range" style="left:346px;width:83px">42D</div>
  <div class="range" style="left:429px;width:125px;font-size:0"></div>
  <div class="nav active" style="left:554px;width:130px">
    <svg width="22" height="20" viewBox="0 0 22 20" fill="none" stroke="#fff" stroke-width="2"><path d="M2 10 11 2l9 8"/><path d="M5 8v10h5v-5h2v5h5V8"/></svg>MODELS</div>
  <div class="nav" style="left:684px;width:156px">
    <svg width="22" height="22" viewBox="0 0 22 22" fill="#222"><circle cx="11" cy="11" r="3"/><g><circle cx="11" cy="3" r="1.5"/><circle cx="11" cy="19" r="1.5"/><circle cx="3" cy="11" r="1.5"/><circle cx="19" cy="11" r="1.5"/><circle cx="5.3" cy="5.3" r="1.5"/><circle cx="16.7" cy="16.7" r="1.5"/><circle cx="16.7" cy="5.3" r="1.5"/><circle cx="5.3" cy="16.7" r="1.5"/><circle cx="11" cy="7" r="1"/><circle cx="11" cy="15" r="1"/><circle cx="7" cy="11" r="1"/><circle cx="15" cy="11" r="1"/></g></svg>SENSITIVITIES</div>
  <div class="nav" style="left:840px;width:156px">
    <svg width="22" height="22" viewBox="0 0 22 22" fill="none" stroke="#222" stroke-width="1.8"><circle cx="6" cy="6" r="4"/><circle cx="16" cy="6" r="4"/><circle cx="6" cy="16" r="4"/><circle cx="16" cy="16" r="4"/></svg>PORTFOLIO</div>
  <div class="nav" style="left:996px;width:139px">
    <svg width="22" height="20" viewBox="0 0 22 20" fill="none" stroke="#222" stroke-width="1.8"><rect x="1" y="1" width="20" height="18"/><path d="M4 15l5-6 4 3 5-7"/></svg>BACKTEST</div>
</header>

<nav>
  <div class="subtab" style="left:65px;top:111px;width:143px;height:32px">EQUITIES</div>
  <div class="subtab" style="left:212px;top:111px;width:143px;height:32px">ETFS</div>
  <div class="subtab" style="left:360px;top:101px;width:143px;height:42px">PAIRS</div>
  <div class="subtab active" style="left:508px;top:92px;width:143px;height:51px">ETF PAIRS</div>
  <div class="subtab" style="left:655px;top:101px;width:143px;height:42px">FACTORS</div>
  <div class="subtab" style="left:803px;top:111px;width:143px;height:32px">NEW TAB TITLE #1</div>
  <div class="subtab" style="left:951px;top:111px;width:143px;height:32px">NEW TAB TITLE #2</div>
  <div class="tab-more"><svg width="12" height="16" viewBox="0 0 12 16" fill="none" stroke="#999" stroke-width="3"><path d="M3 2l6 6-6 6"/></svg></div>
  <div class="tab-add"><svg width="22" height="22" viewBox="0 0 22 22" fill="none" stroke="#fff" stroke-width="1.8"><circle cx="11" cy="11" r="9"/><path d="M11 6v10M6 11h10"/></svg></div>
</nav>

<div class="export"><svg width="24" height="22" viewBox="0 0 24 22" fill="none" stroke="#04305e" stroke-width="2.2"><path d="M15 3h7v7"/><path d="M22 3 11 14"/><path d="M17 12v8H2V6h8"/></svg>Export</div>

<aside class="filters"><span>FILTERS</span>
  <svg width="24" height="24" viewBox="0 0 24 24"><circle cx="12" cy="12" r="11" fill="#04305e" stroke="#fff" stroke-width="1.5"/><path d="M7 12h9M12 8l4 4-4 4" stroke="#fff" stroke-width="2" fill="none"/></svg>
</aside>

<table class="models">
  <colgroup><col style="width:92px"><col style="width:129px"><col style="width:106px"><col style="width:78px"><col span="8" style="width:83px"></colgroup>
  <thead><tr>
    <th class="key">ID <svg width="10" height="7" viewBox="0 0 10 7" fill="none" stroke="#fff" stroke-width="2"><path d="M1 1l4 4 4-4"/></svg></th>
    <th class="key">Sector</th><th class="key">Time</th>
    <th>Quality</th><th>Stat 1</th><th>Stat 2</th><th>Stat 3</th><th>Stat 4</th><th>Stat 5</th><th>Stat 6</th><th>Stat 7</th><th>Stat 8</th>
  </tr></thead>
  <tbody>
    <tr><td class="id">Model 1</td><td class="sector">Materials</td><td>2019-07-03<br>12:15:00.000</td><td>30.2288</td><td>2.01574</td><td>23.305</td><td>-0.149368</td><td>22.3054</td><td>4.63714</td><td>0.945706</td><td>2.81949</td><td>2.60858</td></tr>
    <tr><td class="id">Model 2</td><td class="sector">Industrials</td><td>2019-07-03<br>12:15:00.000</td><td>32.8694</td><td>0.87307</td><td>32.185</td><td>-0.033692</td><td>33.9911</td><td>11.5693</td><td>-0.472968</td><td>-0.830458</td><td>6.80646</td></tr>
    <tr><td class="id">Model 3</td><td class="sector">Consumer<br>Discretionary</td><td>2019-07-03<br>12:15:00.000</td><td>1.66002</td><td>-0.569222</td><td>159.814</td><td>0.0252328</td><td>172.616</td><td>10.2875</td><td>-0.750396</td><td>-0.385309</td><td>4.69146</td></tr>
    <tr><td class="id">Model 4</td><td class="sector">Information<br>Technology</td><td>2019-07-03<br>12:15:00.000</td><td>45.6856</td><td>0.412148</td><td>202.488</td><td>0.0084923</td><td>205.834</td><td>11.9094</td><td>-0.137913</td><td>0.449595</td><td>3.85106</td></tr>
    <tr><td class="id">Model 5</td><td class="sector">Information<br>Technology</td><td>2019-07-03<br>12:15:00.000</td><td>75.7733</td><td>7.06728</td><td>188.605</td><td>0.016913</td><td>161.665</td><td>3.82241</td><td>0.981019</td><td>1.29847</td><td>3.34927</td></tr>
  </tbody>
</table>
</body>
</html>
```